Need to drive pregnant women to my 3d4d ultrasound studio where i provide 4d ultrasound with hyperalistic imaging and gender reveals

Industry/Entity Type

Healthcare

Font styles to use
Decorative
Script

Requirements
Must have
• My Company name Cielo de Nuestra Espera 4D. EVERYTHING HAS TO BE IN SPANISH
Nice to have
• SIMPLE AND NOT TOO BUSY
Should not have
• website

```html
<!DOCTYPE html>
<html lang="es">
<head>
<meta charset="UTF-8">
<title>Cielo de Nuestra Espera 4D – Banner</title>
<link href="https://fonts.googleapis.com/css2?family=Lilita+One&family=Poppins:wght@500;600;700&family=Oswald:wght@500&display=swap" rel="stylesheet">
<style>
  :root{
    --stage:#efeff1;
    --paper:#ffffff;
    --teal:#4cbf9f;
    --violet:#9a5ec9;
    --blush:#dfa3c3;
    --magenta:#bd189b;
    --plum:#4b1d6e;
    --ink:#2a2430;
    --soft-pink:#fdeef5;
    --shirt-light:#b9d6f0;
    --shirt-mid:#6fa6dc;
    --check:#2fae6a;
  }
  *{margin:0;padding:0;box-sizing:border-box}
  html,body{width:1200px;height:919px;overflow:hidden;background:var(--stage)}
  .banner{position:absolute;left:20px;top:169px;width:1160px;height:581px;background:var(--paper);overflow:hidden;box-shadow:0 6px 18px rgba(0,0,0,.18)}
  .banner-shapes{position:absolute;inset:0}
  .headline-top{position:absolute;left:390px;top:40px;font:32px/1 "Lilita One",sans-serif;color:var(--teal);letter-spacing:1px;white-space:nowrap}
  .headline-main{position:absolute;left:386px;top:72px;font:104px/1 "Lilita One",sans-serif;color:var(--violet);letter-spacing:1px;white-space:nowrap}
  .headline-tail{position:absolute;left:858px;top:86px;font:36px/1.05 "Lilita One",sans-serif;color:var(--blush);white-space:nowrap}
  .brand{position:absolute;left:990px;top:52px;width:124px;text-align:center}
  .brand-dot{width:44px;height:44px;border-radius:50%;background:var(--soft-pink);margin:0 auto 8px}
  .brand-name{font:600 13px/1.25 "Poppins",sans-serif;color:var(--magenta)}
  .features{position:absolute;left:502px;top:196px;list-style:none;font:600 19px/1.27 "Poppins",sans-serif;color:var(--ink);white-space:nowrap}
  .features li{position:relative;padding-left:29px}
  .features li.check::before{content:"";position:absolute;left:0;top:4px;width:20px;height:20px;border-radius:50%;background:var(--check)}
  .features li.check::after{content:"";position:absolute;left:6px;top:9px;width:8px;height:5px;border-left:2.5px solid #fff;border-bottom:2.5px solid #fff;transform:rotate(-45deg)}
  .tagline{position:absolute;left:502px;top:330px;font:30px/0.95 "Lilita One",sans-serif;white-space:nowrap}
  .tagline .accent{color:var(--teal)}
  .tagline .deep{color:var(--plum)}
  .frame{position:absolute;background:#fff;padding:8px;box-shadow:0 3px 10px rgba(0,0,0,.2)}
  .frame-scan{left:793px;top:193px;width:160px;height:192px;transform:rotate(-2deg)}
  .frame-baby{left:921px;top:222px;width:196px;height:214px;transform:rotate(4deg)}
  .frame .fill{width:100%;height:100%}
  .frame-scan .fill{background:linear-gradient(135deg,#c87a2a,#7a3c10)}
  .frame-baby .fill{background:linear-gradient(135deg,#f0c6b4,#c98e80)}
  .contact{position:absolute;left:455px;top:490px;color:#fff;white-space:nowrap}
  .phone{display:flex;align-items:center;gap:6px;font:31px/1 "Lilita One",sans-serif;letter-spacing:1px}
  .phone svg{width:24px;height:24px}
  .handle{font:600 17px/1 "Poppins",sans-serif;margin-top:12px;padding-left:3px}
  .divider{position:absolute;left:792px;top:488px;width:2px;height:62px;background:var(--teal)}
  .cta{position:absolute;left:816px;top:490px;color:#fff;white-space:nowrap}
  .cta-title{font:500 34px/1 "Oswald",sans-serif;letter-spacing:.2px;transform:scaleX(.85);transform-origin:left}
  .cta-sub{font:600 14px/1 "Poppins",sans-serif;margin-top:9px}
</style>
</head>
<body>
<main class="banner">
  <svg class="banner-shapes" viewBox="0 0 1160 581" width="1160" height="581">
    <defs>
      <linearGradient id="shirt" x1="0" y1="0" x2="1" y2="1">
        <stop offset="0" stop-color="var(--shirt-light)"/>
        <stop offset="1" stop-color="var(--shirt-mid)"/>
      </linearGradient>
    </defs>
    <path d="M440 292 C540 300 610 312 690 280 C770 250 820 200 900 196 L1160 196 V581 H440 Z" fill="var(--soft-pink)"/>
    <path d="M340 581 C390 470 450 425 540 430 C640 440 720 440 810 412 C900 385 960 432 1040 430 C1110 428 1145 400 1160 370 V581 Z" fill="var(--magenta)"/>
    <path role="img" aria-label="Foto de una mujer embarazada con camisa azul a rayas sosteniendo una impresión de ecografía" d="M0 0 H420 C470 140 470 340 430 581 H0 Z" fill="url(#shirt)"/>
  </svg>

  <p class="headline-top">ASÓMATE AL</p>
  <h1 class="headline-main">MILAGRO</h1>
  <p class="headline-tail">DE LA<br>VIDA</p>

  <div class="brand">
    <div class="brand-dot"></div>
    <p class="brand-name">Cielo de Nuestra Espera 4D</p>
  </div>

  <ul class="features">
    <li class="check">Ultrasonido 4D</li>
    <li class="check">Revelación de Género</li>
    <li>Imágenes<br>Hiperrealistas</li>
  </ul>

  <p class="tagline"><span class="accent">RECUERDOS</span><br><span class="deep">QUE DURAN<br>TODA LA VIDA</span></p>

  <figure class="frame frame-scan"><div class="fill" role="img" aria-label="Imagen de ultrasonido 3D de un bebé"></div></figure>
  <figure class="frame frame-baby"><div class="fill" role="img" aria-label="Foto de un recién nacido dormido"></div></figure>

  <div class="contact">
    <p class="phone">
      <svg viewBox="0 0 26 26"><circle cx="13" cy="13" r="13" fill="var(--teal)"/><path d="M9 7 l3 3 -1.5 2 c1 2 2.5 3.5 4.5 4.5 l2-1.5 3 3 -2 2 c-5 0-11-6-11-11z" fill="#fff"/></svg>
      +1 555-014-2738
    </p>
    <p class="handle">@Cielo-de-Nuestra-Espera-4D</p>
  </div>
  <div class="divider"></div>
  <div class="cta">
    <p class="cta-title">RESERVA TU SESIÓN EN</p>
    <p class="cta-sub">Nuestro Estudio de Ultrasonido 3D/4D</p>
  </div>
</main>
</body>
</html>
```